Oakmere Animal Care Group of Central Pennsylvania

I need a business card design for a new company in Harrisburg PA called "Animal Care Oakmere Group of Central PA". I will be providing relief services for veterinarians who need coverage during vacations; sick/maternity leave, etc. I would like to see the veterinarian symbol incorporated in the design in combination with animals (dogs /cats/birds/reptiles an pocket pets). Include My full name: Tomás R. Quintaval DVM, MLAS, BS. Also include my e mail (dvmtrq@mailbrook.net) and phone number 5552846017

Target Market(s)

Small Animal Veterinarian, practice owner

Industry/Entity Type

Business

Contact Information for Business Card

Oakmere Animal Care Group of Central PA

Font styles to use
Script

Requirements
Must have
• Veterinarian caduceus (see image) and Small animals (pets) within the logo.
Nice to have
• Give a sense of relaxation (vacationing)
Should not have
• Large animals, i.e. horses, cows, zoo animals...

```html
<!DOCTYPE html>
<html lang="en">
<head>
<meta charset="utf-8">
<title>Animal Care Oakmere Group of Central PA – Business Card</title>
<link rel="stylesheet" href="https://fonts.googleapis.com/css2?family=Great+Vibes&family=Open+Sans:wght@400;600&family=Cinzel:wght@600&display=swap">
<style>
  :root {
    --page-bg: #e9e6e1;
    --card-white: #ffffff;
    --brand-red: #b3232a;
    --brand-black: #0b0b0b;
    --ink: #111111;
  }
  * { margin: 0; padding: 0; box-sizing: border-box; }
  html, body { width: 1200px; height: 818px; overflow: hidden; }
  body {
    background: var(--page-bg);
    display: flex;
    align-items: center;
    justify-content: center;
  }
  .business-card {
    position: relative;
    width: 860px;
    height: 490px;
    background: var(--card-white);
    overflow: hidden;
    box-shadow: 0 10px 30px rgba(0,0,0,0.18);
  }
  .card-shapes { position: absolute; inset: 0; }
  .contact-block {
    position: absolute;
    left: 330px;
    top: 70px;
    width: 320px;
  }
  .employee-name {
    font-family: "Great Vibes", cursive;
    color: var(--brand-red);
    font-size: 56px;
    line-height: 1.1;
    margin-bottom: 14px;
  }
  .contact-line {
    font-family: "Open Sans", sans-serif;
    color: var(--ink);
    font-size: 25px;
    line-height: 1.45;
    letter-spacing: 0.3px;
  }
  .brand-block {
    position: absolute;
    left: 270px;
    top: 300px;
    width: 420px;
    display: flex;
    align-items: center;
    gap: 20px;
  }
  .brand-circle {
    flex: none;
    width: 96px;
    height: 96px;
    border-radius: 50%;
    border: 6px solid var(--brand-red);
  }
  .brand-name {
    font-family: "Cinzel", serif;
    font-weight: 600;
    color: var(--ink);
    font-size: 21px;
    line-height: 1.35;
    letter-spacing: 0.5px;
  }
</style>
</head>
<body>
  <div class="business-card">
    <svg class="card-shapes" width="860" height="490" viewBox="0 0 860 490" aria-hidden="true">
      <path class="red-band" d="M0,0 L250,0 Q40,245 230,490 L0,490 Z" fill="var(--brand-red)"/>
      <path class="black-band" d="M650,0 Q860,245 640,490 L860,490 L860,0 Z" fill="var(--brand-black)"/>
    </svg>

    <div class="contact-block">
      <p class="employee-name">Employee Name</p>
      <p class="contact-line">5552846017</p>
      <p class="contact-line">dvmtrq@mailbrook.net</p>
    </div>

    <div class="brand-block">
      <span class="brand-circle"></span>
      <p class="brand-name">Animal Care Oakmere Group<br>of Central PA</p>
    </div>
  </div>
</body>
</html>
```